Climb Past Tuesday - Nobody Writes My Ending

The front book cover. The book will include life lessons I've learned through three breast cancer (Pink Ribbon) diagnoses and how to create positivity through adversity. Lessons that most people don't think of until they're hit with a life-altering setback. The chapters include Imposter Syndrome (Pink Ribbon Warriors don't have time to debate if they're good enough, they just jump in and get it done because life is too short), Stand Your Ground (stick up for your beliefs and advocate for yourself), The Flip Side of It's All About Me (like an emergency rescuer who must equip themselves first, you need to take care of yourself first). The main message in the book is when others say you CAN'T, I say you CAN! Warrior means being strong no matter what life deals you. I've included a word document with more information.
Updates

Please note: Pink is only to be an accent color. I'd like my brand colors to be included. The title of the book is to be the focus with an image to add to the book cover appeal.

Target Market(s)

professionals with a growth mindset and people going through adversity

Industry/Entity Type

HR, Libraries, Hosppitality,

Font styles to use
Sans Serif

Colors
6B429C
8869AF
B7A5CE
E3DAEB
F3F0F8

Requirements
Must have
• Be original. Cover to be appealing to male and female buyers. Incorporate my purple brand color. Be creative and unique.
Nice to have
• Although I have offered a suggestion, I'm open to a creative cover that wows me.
Should not have
• No cartoon image or stock image

```html
<!DOCTYPE html>
<html lang="en">
<head>
<meta charset="utf-8">
<title>Nobody Writes My Ending – Book Cover</title>
<link rel="stylesheet" href="https://fonts.googleapis.com/css2?family=Jost:ital,wght@0,500;0,600;1,500&display=swap">
<style>
  :root {
    --backdrop: #262626;
    --paper: #ffffff;
    --purple-deep: #6a1aa6;
    --purple-bright: #9b50e8;
    --gold-light: #d0b465;
    --gold-dark: #a2802e;
    --glove-dark: #5e2d86;
    --glove-mid: #a551c0;
    --glove-light: #e39cf2;
    --tear-shadow: #d9d9d9;
    --subtitle: #f8dc8e;
    --author: #ffffff;
  }
  * { margin: 0; padding: 0; box-sizing: border-box; }
  html, body {
    width: 1200px; height: 1200px; overflow: hidden;
    background: var(--backdrop);
    font-family: 'Jost', 'Futura', sans-serif;
  }
  .cover {
    position: absolute; left: 236px; top: 17px;
    width: 728px; height: 1166px;
    background: var(--paper); overflow: hidden;
  }
  .title { position: absolute; left: 0; top: 0; width: 728px; height: 538px; }
  .title text { font-family: 'Jost', 'Futura', sans-serif; }
  .punch-art {
    position: absolute; left: 120px; top: 545px;
    width: 500px; height: 520px;
    background:
      radial-gradient(ellipse 44% 46% at 50% 52%, var(--glove-light) 0%, var(--glove-mid) 45%, var(--glove-dark) 78%, rgba(94,45,134,0) 80%),
      radial-gradient(ellipse 52% 52% at 50% 50%, var(--tear-shadow) 0%, rgba(255,255,255,0) 75%);
  }
  .subtitle {
    position: absolute; left: 163px; top: 728px; width: 290px;
    text-align: center; color: var(--subtitle); font-weight: 500; line-height: 1.12;
  }
  .subtitle .lead { display: block; font-size: 40px; font-weight: 600; line-height: 1.05; }
  .subtitle .rest { display: block; font-size: 24px; }
  .author-band {
    position: absolute; left: 0; bottom: 0; width: 728px; height: 68px;
    background: linear-gradient(90deg, var(--gold-dark), var(--gold-light) 50%, var(--gold-dark));
    display: flex; align-items: center; justify-content: center;
  }
  .author-name { color: var(--author); font-size: 38px; font-weight: 600; letter-spacing: 0.5px; white-space: nowrap; }
</style>
</head>
<body>
  <div class="cover">
    <svg class="title" viewBox="0 0 703 520" aria-label="Nobody Writes My Ending!">
      <defs>
        <linearGradient id="purpleInk" x1="0" y1="0" x2="1" y2="0">
          <stop offset="0" stop-color="var(--purple-deep)"/>
          <stop offset="0.55" stop-color="var(--purple-bright)"/>
          <stop offset="1" stop-color="var(--purple-deep)"/>
        </linearGradient>
        <linearGradient id="goldInk" x1="0" y1="0" x2="1" y2="0">
          <stop offset="0" stop-color="var(--gold-light)"/>
          <stop offset="0.5" stop-color="var(--gold-dark)"/>
          <stop offset="1" stop-color="var(--gold-light)"/>
        </linearGradient>
      </defs>
      <text x="52" y="223" font-size="176" font-weight="500" fill="url(#purpleInk)" textLength="606" lengthAdjust="spacingAndGlyphs">NOBODY</text>
      <text x="97" y="362" font-size="128" font-weight="500" fill="url(#goldInk)" textLength="495" lengthAdjust="spacingAndGlyphs">WRITES MY</text>
      <text x="150" y="469" font-size="104" font-weight="500" font-style="italic" fill="url(#goldInk)" textLength="380" lengthAdjust="spacingAndGlyphs">ENDING!</text>
    </svg>

    <div class="punch-art" role="img" aria-label="Purple boxing glove punching through torn white paper"></div>

    <p class="subtitle">
      <span class="lead">Hard Truths</span>
      <span class="rest">From A Three-Time</span>
      <span class="rest">Survivor &amp; Fighter</span>
    </p>

    <div class="author-band">
      <span class="author-name">Rae Holloway, CPDC, MHRP, CSL</span>
    </div>
  </div>
</body>
</html>
```